New Web Site Design - Tallow Ridge Communication Solutions

We are looking for a completely new web site design. Tallow Ridge Communication Solutions is a full service company providing PBX and IP/Cloud Based phone systems. We also sell and install video camera surveillance systems and provide low voltage cabling services (CAT5 and CAT3). We are looking for something professional looking. We want to be able to showcase our vendor partners as well as be able to show photos of some of the work we have done. We will also want to be able to post PDF brochures as well as make changes to the website ourselves.

Target Market(s)

Commercial

Industry/Entity Type

Communication

Coding

Coded - Design and coding required

Number of Pages Required

5+ page

Font styles to use
Sans Serif

Colors
0455a3

Requirements
Must have
• Ability to upload PDF brochures
• Professional look and feel
• Ability to upload and easily insert job photos
• Thinking it should have at least 6 pages: Main page, phone systems and services page, carrier services page, video surveillance systems and service page, low voltage cabling services page, contact us page

```html
<!DOCTYPE html>
<html lang="en">
<head>
<meta charset="utf-8">
<title>Tallow Ridge Communication Solutions</title>
<link href="https://fonts.googleapis.com/css2?family=Roboto+Condensed:wght@400;700&family=Roboto+Slab:wght@400&family=Arimo:wght@400;700&display=swap" rel="stylesheet">
<style>
:root{
  --brand:#0455a3;
  --brand-dark:#033f7a;
  --navy:#0b2340;
  --ink:#222;
  --muted:#555;
  --band:#efefef;
  --rule:#cfcfcf;
  --field:#6a6a6a;
}
*{margin:0;padding:0;box-sizing:border-box}
html,body{width:1200px;height:2344px;overflow:hidden}
body{font-family:"Arimo",Arial,sans-serif;color:var(--ink);background:#fff;position:relative}
.heading{font-family:"Roboto Condensed",Arial,sans-serif;font-weight:400;color:#222;text-align:center}
a{color:var(--brand-dark);text-decoration:underline}

/* header */
.site-header{position:absolute;left:0;top:0;width:1200px;height:144px;
  background:linear-gradient(100deg,#eef6fb 0%,#d9eef8 35%,#e6f1fb 60%,#ece4f6 100%)}
.brand-name{position:absolute;left:100px;top:30px;width:240px;font-family:"Roboto Condensed",sans-serif;font-size:27px;line-height:1.1;color:var(--navy)}
.social{position:absolute;right:94px;top:20px;display:flex;align-items:center;gap:10px;font-size:13px;color:var(--navy)}
.social span.dot{width:28px;height:28px;border:2px solid var(--navy);border-radius:50%}
.brochure{position:absolute;left:686px;top:72px;display:flex;align-items:center}
.brochure svg{margin-right:-4px}
.brochure-btn{background:var(--brand);color:#fff;font-family:"Roboto Condensed",sans-serif;font-size:18px;padding:8px 18px 8px 20px}
.call{position:absolute;left:938px;top:78px;display:flex;gap:10px;align-items:center}
.call-label{font-size:14px;font-weight:700;color:var(--navy)}
.call-number{font-size:23px;color:var(--brand)}

/* nav */
.main-nav{position:absolute;left:0;top:144px;width:1200px;height:51px;background:var(--brand);display:flex;padding-left:82px}
.main-nav a{font-family:"Roboto Slab",Georgia,serif;color:#fff;text-decoration:none;font-size:15px;padding:0 9px;height:51px;line-height:51px;border-right:1px solid #3a7cc0;white-space:nowrap}
.main-nav a:last-child{border-right:0}

/* hero */
.hero{position:absolute;left:0;top:195px;width:1200px;height:445px;
  background:linear-gradient(90deg,#e9e6e0 0%,#d8d4cc 30%,#9b9a97 55%,#6a6b6d 75%,#e2e0dc 100%)}
.hero-title{position:absolute;left:86px;top:117px;font-family:"Roboto Condensed",sans-serif;font-size:42px;line-height:61px;color:#3a3a3a}
.hero-arrow{position:absolute;top:203px;width:36px;height:32px;background:#333;display:flex;align-items:center;justify-content:center}

/* welcome */
.welcome{position:absolute;left:0;top:640px;width:1200px;height:240px}
.welcome h1{margin-top:36px;font-size:30px}
.rule{position:relative;margin:12px auto 0;height:1px;background:var(--rule)}
.rule::after{content:"";position:absolute;left:50%;top:-2px;width:64px;height:4px;margin-left:-32px;background:var(--brand)}
.welcome p{width:980px;margin:22px auto 0;font-size:13px;line-height:21px;text-align:center;color:#333}
.read-more{display:block;width:max-content;margin:4px auto 0;font-size:13px}

/* products */
.products{position:absolute;left:0;top:880px;width:1200px;height:425px;background:var(--band)}
.products h2{margin-top:28px;font-size:30px}
.products .lead{text-align:center;font-size:13px;margin-top:6px;color:#333}
.service-list{position:absolute;top:136px;left:0;width:1200px}
.service{position:absolute;width:220px;margin-left:-110px;text-align:center}
.service .icon{width:115px;height:115px;margin:0 auto;border-radius:50%;border:3px solid #222;padding:4px}
.service .icon div{width:100%;height:100%;border-radius:50%;background:var(--brand);display:flex;align-items:center;justify-content:center}
.service h3{font-family:"Roboto Condensed",sans-serif;font-weight:400;font-size:19px;margin-top:14px;white-space:nowrap}
.service p{width:165px;margin:10px auto 0;font-size:13px;line-height:18px;color:var(--muted)}
.service a{display:block;width:max-content;margin:10px auto 0;font-size:13px}

/* gallery */
.gallery{position:absolute;left:0;top:1305px;width:1200px;height:437px}
.gallery h2{margin-top:48px;font-size:30px}
.gallery .rule{width:180px}
.cards{position:absolute;top:114px;left:83px;display:flex;gap:12px}
.card{width:250px;height:231px;border:4px solid #c9c9c9;position:relative}
.card .photo{width:100%;height:100%}
.card .caption{position:absolute;left:0;bottom:0;width:100%;height:46px;background:rgba(0,0,0,.6);color:#fff;font-family:"Roboto Condensed",sans-serif;font-size:18px;line-height:46px;text-align:center}
.pager{position:absolute;top:367px;left:568px;display:flex;gap:8px}
.pager span{width:27px;height:23px;border:1px solid #555;display:flex;align-items:center;justify-content:center}
.pager span.on{border-color:var(--brand)}

/* vendors */
.vendors{position:absolute;left:0;top:1742px;width:1200px;height:242px;background:var(--band)}
.vendors h2{margin-top:28px;font-size:30px}
.vendors .rule{width:224px}
.badge-row{position:absolute;top:126px;left:93px;display:flex;align-items:center;gap:39px}
.badge{height:62px}
.vendor-arrow{position:absolute;top:147px}

/* footer */
.site-footer{position:absolute;left:0;top:1984px;width:1200px;height:321px;background:linear-gradient(160deg,#454545,#353535)}
.contact{position:absolute;left:97px;top:32px;color:#fff}
.contact h4{font-family:"Roboto Condensed",sans-serif;font-weight:400;font-size:21px;margin-bottom:22px}
.contact-item{display:flex;gap:14px;margin-bottom:17px;font-size:13px;line-height:18px}
.contact-item svg{flex:none;margin-top:2px}
.inquiry{position:absolute;left:466px;top:32px;width:620px;height:220px;background:rgba(110,110,110,.55);border-top:3px solid #777;color:#fff;padding:16px 14px}
.inquiry-head{display:flex;justify-content:space-between;align-items:center}
.inquiry-title{display:flex;gap:8px;align-items:center;font-family:"Roboto Condensed",sans-serif;font-size:19px}
.inquiry-note{font-family:"Roboto Slab",Georgia,serif;font-size:14px}
.fields{position:absolute;left:14px;top:66px;width:592px}
.field{position:absolute;background:var(--field);color:#ddd;font-size:12px;padding:0 12px;line-height:38px;height:38px}
.spam{position:absolute;left:14px;top:196px;font-size:10px;display:flex;gap:6px;align-items:center}
.spam i{width:11px;height:11px;background:#fff;display:block}
.submit{position:absolute;right:20px;top:192px;background:var(--brand);color:#fff;font-weight:700;font-size:14px;padding:3px 14px}
.copyright{position:absolute;left:0;top:2305px;width:1200px;height:39px;background:#f2f2f2;text-align:center;line-height:39px;font-size:12px;color:var(--brand)}
</style>
</head>
<body>

<header class="site-header">
  <div class="brand-name">Tallow Ridge Communication Solutions</div>
  <div class="social">Follow Us On <span class="dot"></span><span class="dot"></span><span class="dot"></span></div>
  <div class="brochure">
    <svg width="42" height="50" viewBox="0 0 42 50"><rect x="3" y="3" width="34" height="44" fill="#fff" stroke="#0455a3" stroke-width="3"/><path d="M20 14v16m-7-7 7 7 7-7M12 36h16" stroke="#0455a3" stroke-width="3" fill="none"/></svg>
    <span class="brochure-btn">Download Our Brochure</span>
  </div>
  <div class="call">
    <svg width="32" height="32" viewBox="0 0 32 32"><circle cx="16" cy="16" r="14" fill="none" stroke="#0b2340" stroke-width="2"/><path d="M11 8c-2 2-2 6 1 10s7 6 9 5l2-2-3-3-2 1c-2-1-4-3-5-5l1-2-3-4z" fill="#0455a3"/></svg>
    <div><div class="call-label">Call Us Today</div><div class="call-number">555-014-2290</div></div>
  </div>
</header>

<nav class="main-nav">
  <a>About Us</a><a>Phone Systems &amp; Services</a><a>Low Voltage Cabling Service</a><a>Carrier Services</a><a>Video Surveillance Systems Service</a><a>Contact Us</a>
</nav>

<section class="hero" role="img" aria-label="Photo of a desk telephone on an office desk beside a pen holder and plant">
  <div class="hero-title">Hosted PBX<br>The Business Phone<br>System in the Cloud</div>
  <span class="hero-arrow" style="left:6px"><svg width="12" height="14"><path d="M9 2 3 7l6 5" stroke="#fff" stroke-width="3" fill="none"/></svg></span>
  <span class="hero-arrow" style="right:6px"><svg width="12" height="14"><path d="M3 2l6 5-6 5" stroke="#fff" stroke-width="3" fill="none"/></svg></span>
</section>

<section class="welcome">
  <h1 class="heading">Welcome to Tallow Ridge Communications Solutions</h1>
  <div class="rule" style="width:668px"></div>
  <p>Lorem ipsum dolor sit amet, consectetuer adipiscing elit, sed diam nonummy nibh euismod tincidunt ut laoreet dolore magna aliquam erat volutpat. Ut wisi enim ad minim veniam, quis nostrud exerci tation ullamcorper suscipit lobortis nisl ut aliquip ex ea commodo consequat. Duis autem vel eum iriure dolor in hendrerit in vulputate velit esse molestie consequat, vel illum dolore eu feugiat nulla facilisis at vero eros et accumsan et iusto odio dignissim qui blandit praesent luptatum zzril delenit augue duis dolore te feugait nulla facilisi.</p>
  <a class="read-more">Read more</a>
</section>

<section class="products">
  <h2 class="heading">Product &amp; Services</h2>
  <p class="lead">Lorem ipsum dolor sit amet, consectetur adipiscing elit. Aenean et dignissim sem,  interdum risus. Vestibulum consectetur</p>
  <div class="rule" style="width:704px"></div>
  <div class="service-list">
    <div class="service" style="left:172px">
      <div class="icon"><div><svg width="56" height="48" viewBox="0 0 56 48" fill="#fff"><rect x="2" y="4" width="12" height="40" rx="4"/><rect x="18" y="8" width="36" height="36" rx="3"/><rect x="23" y="12" width="26" height="8" fill="#0455a3"/><g fill="#0455a3"><rect x="23" y="24" width="6" height="5"/><rect x="33" y="24" width="6" height="5"/><rect x="43" y="24" width="6" height="5"/><rect x="23" y="33" width="6" height="5"/><rect x="33" y="33" width="6" height="5"/><rect x="43" y="33" width="6" height="5"/></g></svg></div></div>
      <h3>PBX Phone Systems</h3>
      <p>Lorem ipsum dolr sit amet, consectetur adipiscing elit. Aenean et dign.</p>
      <a>Read more</a>
    </div>
    <div class="service" style="left:384px">
      <div class="icon"><div><svg width="64" height="44" viewBox="0 0 64 44" fill="#fff"><path d="M14 40a12 12 0 0 1-2-24 16 16 0 0 1 30-6 12 12 0 0 1 10 30z"/><rect x="22" y="18" width="20" height="16" fill="#0455a3"/><rect x="25" y="21" width="14" height="10" fill="#fff"/></svg></div></div>
      <h3>IP/Cloud Phone System</h3>
      <p>Lorem ipsum dolr sit amet, consectetur adipiscing elit. Aenean et dign.</p>
      <a>Read more</a>
    </div>
    <div class="service" style="left:609px">
      <div class="icon"><div><svg width="62" height="44" viewBox="0 0 62 44" fill="#fff"><path d="M4 10l40 8-2 12L2 22z"/><rect x="44" y="18" width="8" height="8"/><path d="M40 30l4 8h14v-6h-9l-3-6z"/></svg></div></div>
      <h3>Video camera surveillance</h3>
      <p>Lorem ipsum dolr sit amet, consectetur adipiscing elit. Aenean et dign.</p>
      <a>Read more</a>
    </div>
    <div class="service" style="left:828px">
      <div class="icon"><div><svg width="44" height="56" viewBox="0 0 44 56"><rect x="10" y="6" width="22" height="44" rx="4" fill="none" stroke="#fff" stroke-width="4"/><circle cx="21" cy="42" r="2" fill="#fff"/><path d="M34 10a10 10 0 0 1 0 14M38 6a16 16 0 0 1 0 22" stroke="#fff" stroke-width="3" fill="none"/></svg></div></div>
      <h3>Carrier Service</h3>
      <p>Lorem ipsum dolr sit amet, consectetur adipiscing elit. Aenean et dign.</p>
      <a>Read more</a>
    </div>
    <div class="service" style="left:1031px">
      <div class="icon"><div><svg width="58" height="50" viewBox="0 0 58 50" fill="none" stroke="#fff" stroke-width="3"><path d="M6 40c10-4 14-18 26-16s12 14 20 10"/><rect x="2" y="36" width="10" height="8" fill="#fff"/><rect x="46" y="30" width="10" height="8" fill="#fff"/><path d="M20 4l4 10M28 2l2 10M36 4l-2 10"/></svg></div></div>
      <h3>Low Voltage Cabling</h3>
      <p>Lorem ipsum dolr sit amet, consectetur adipiscing elit. Aenean et dign.</p>
      <a>Read more</a>
    </div>
  </div>
</section>

<section class="gallery">
  <h2 class="heading">Project Gallery</h2>
  <div class="rule"></div>
  <div class="cards">
    <div class="card"><div class="photo" role="img" aria-label="Photo of an office desk phone" style="background:linear-gradient(135deg,#e8ebe6,#6d6f70)"></div><div class="caption">Lorem Ispim is Dummmy</div></div>
    <div class="card"><div class="photo" role="img" aria-label="Photo of a technician mounting a security camera" style="background:linear-gradient(160deg,#3f7ac0,#9bb4c8 60%,#c06a4e)"></div><div class="caption">Lorem Ispim is Dummmy</div></div>
    <div class="card"><div class="photo" role="img" aria-label="Photo of a cabling technician holding a coil of cable" style="background:linear-gradient(160deg,#d6dde3,#3c4658)"></div><div class="caption">Lorem Ispim is Dummmy</div></div>
    <div class="card"><div class="photo" role="img" aria-label="Photo of hands using a desk phone" style="background:linear-gradient(135deg,#f2f2f2,#8d8f91 55%,#2d2e30)"></div><div class="caption">Lorem Ispim is Dummmy</div></div>
  </div>
  <div class="pager">
    <span><svg width="10" height="12"><path d="M7 1 2 6l5 5" stroke="#333" stroke-width="2" fill="none"/></svg></span>
    <span class="on"><svg width="10" height="12"><path d="M3 1l5 5-5 5" stroke="#0455a3" stroke-width="2" fill="none"/></svg></span>
  </div>
</section>

<section class="vendors">
  <h2 class="heading">Our Vendor Partners</h2>
  <div class="rule"></div>
  <svg class="vendor-arrow" style="left:60px" width="14" height="26"><path d="M12 2 2 13l10 11" stroke="#777" stroke-width="2" fill="none"/></svg>
  <div class="badge-row">
    <div class="badge" style="width:96px;border-radius:50%;background:#c9a06a"></div>
    <div class="badge" style="width:138px;height:46px;background:#e32222"></div>
    <div class="badge" style="width:104px;background:#0b5a9e"></div>
    <div class="badge" style="width:132px;height:56px;background:#2f9a3c"></div>
    <div class="badge" style="width:224px;height:40px;background:#e2232a"></div>
    <div class="badge" style="width:104px;background:#0b5a9e"></div>
  </div>
  <svg class="vendor-arrow" style="left:1128px" width="14" height="26"><path d="M2 2l10 11L2 24" stroke="#777" stroke-width="2" fill="none"/></svg>
</section>

<footer class="site-footer" role="img" aria-label="Street map of the office neighbourhood behind the contact details">
  <div class="contact">
    <h4>Contact Information</h4>
    <div class="contact-item"><svg width="14" height="18" viewBox="0 0 14 18"><path d="M7 17S1 10 1 6.5a6 6 0 0 1 12 0C13 10 7 17 7 17z" fill="#fff"/><circle cx="7" cy="6.5" r="2.2" fill="#444"/></svg><div>Postal Address<br>Harlow Point, Eastvale</div></div>
    <div class="contact-item"><svg width="14" height="16" viewBox="0 0 14 16"><path d="M3 1c-2 2-2 6 1 9s7 5 9 4l1-2-3-3-2 1c-2-1-3-2-4-4l1-2z" fill="#fff"/></svg><div>Telephone<br>0400 555 218</div></div>
    <div class="contact-item"><svg width="14" height="12" viewBox="0 0 14 12"><rect x="0" y="1" width="14" height="10" fill="#fff"/><path d="M0 1l7 5 7-5" stroke="#444" fill="none"/></svg><div>Email<br>mara@tallowridgecomms.net</div></div>
    <div class="contact-item"><svg width="14" height="14"><circle cx="7" cy="7" r="6" fill="#fff"/></svg><div>Facebook<br>/tallowridgecomms</div></div>
  </div>
  <form class="inquiry">
    <div class="inquiry-head">
      <div class="inquiry-title"><svg width="22" height="16" viewBox="0 0 22 16"><rect width="22" height="16" fill="#fff"/><path d="M0 0l11 9 11-9" stroke="#777" stroke-width="2" fill="none"/></svg>QUICK INQUIRY</div>
      <div class="inquiry-note">We look forward to working with you!</div>
    </div>
    <div class="fields">
      <div class="field" style="left:0;top:0;width:232px">First Name</div>
      <div class="field" style="left:242px;top:0;width:350px">Email Address</div>
      <div class="field" style="left:0;top:44px;width:232px">Last Name</div>
      <div class="field" style="left:242px;top:44px;width:350px;height:82px">Message</div>
      <div class="field" style="left:0;top:88px;width:232px">Phone</div>
    </div>
    <div class="spam"><i></i>Please tick so that we know you are not a spam bot</div>
    <div class="submit">Submit</div>
  </form>
</footer>

<div class="copyright">© 2015  TallowRidgeCommunicationSolutions  All rights reserved</div>

</body>
</html>
```